Banner for construction site to identify developer

we need a 4 foot by 8 foot banner to hang on the fence of a residential townhome development in Phoenix, Arizona that identifies Tolvane Holdings as the company behind the development/project. Also needs to include the logo, phone number, and web address. Would like to stick with the blue colors provided in the attached logo. The blues should stay the same but the letters in the logo can change to another color if necessary. Feel free to use "Tolvane Holdings" in place of "Tolvane Holdings Group". Looking for use of colors/design to take up space so banner is not just text with a logo.

Target Market(s)

drive by traffic looking at the site

Industry/Entity Type

Real Estate

Colors
0054AA
0677BA
7BADD7
CADEEF
E8F1F8

Requirements
Must have
• company name, phone number and web address

```html
<!DOCTYPE html>
<html lang="en">
<head>
<meta charset="utf-8">
<title>Tolvane Holdings – Site Banner</title>
<link rel="stylesheet" href="https://fonts.googleapis.com/css2?family=Cinzel:wght@600&family=Kumbh+Sans:wght@700&display=swap">
<style>
  :root {
    --page-bg: #e8f1f8;
    --banner-top: #2b4f96;
    --banner-mid: #3d63b3;
    --banner-bottom: #4a72c2;
    --brand-sky: #3a9edb;
    --web-blue: #45aee6;
    --text-white: #ffffff;
    --text-shadow: #0b2350;
  }
  html, body {
    margin: 0;
    padding: 0;
    width: 1200px;
    height: 734px;
    overflow: hidden;
    background: var(--page-bg);
  }
  .canvas {
    position: relative;
    width: 1200px;
    height: 734px;
  }
  .banner {
    position: absolute;
    left: 40px;
    top: 229px;
    width: 1120px;
    height: 276px;
    background: linear-gradient(180deg, var(--banner-top) 0%, var(--banner-mid) 55%, var(--banner-bottom) 100%);
    box-shadow: inset 0 0 60px rgba(10, 30, 80, 0.35);
  }
  .brand {
    position: absolute;
    left: 178px;
    top: 92px;
    display: flex;
    align-items: center;
    gap: 22px;
  }
  .brand-square {
    width: 62px;
    height: 62px;
    background: var(--brand-sky);
  }
  .brand-name {
    font-family: "Cinzel", serif;
    font-weight: 600;
    font-size: 66px;
    line-height: 1;
    color: var(--text-white);
    letter-spacing: 1px;
    white-space: nowrap;
  }
  .contact {
    position: absolute;
    top: 216px;
    font-family: "Kumbh Sans", sans-serif;
    font-weight: 700;
    font-size: 27px;
    line-height: 1;
    white-space: nowrap;
    text-shadow: 0 0 1px var(--text-shadow);
  }
  .contact-phone {
    left: 178px;
    color: var(--text-white);
  }
  .contact-web {
    right: 120px;
    color: var(--web-blue);
  }
</style>
</head>
<body>
<div class="canvas">
  <section class="banner" role="img" aria-label="Blue construction fence banner with a subtle hexagon texture">
    <div class="brand">
      <div class="brand-square"></div>
      <div class="brand-name">Tolvane Holdings</div>
    </div>
    <div class="contact contact-phone">Phone : +6281355501247</div>
    <div class="contact contact-web">www.tolvaneholdings.com</div>
  </section>
</div>
</body>
</html>
```